High Tech Real Estate Startup needs a business card

We are developing an innovative real estate marketing product based around advanced search and virtual reality.

We talk to people, we need business cards.

Target Market(s)

The target market is technology professionals and realtors.

Contact Information for Business Card

The information to be included will include

Name
Title
Phone Number
E-mail Address
www.zelquin.com

It should use simple iconography for each one of those fields.

Font styles to use
Other font styles liked:
• Co, Jubilat, Avenir

Colors

Designer to choose colors to be used in the design.

Requirements
Must have
• Clean aesthetic,
• Good use of negative space.
• It should use our company logo, shown in the attached file. It is able to use the negative of that logo (coloured font and white background) and I have attached other acceptable accent colours in a swatch file.
Should not have
• Should not be too busy
• No extraneous text (slogans, tag lines etc)

```html
<!DOCTYPE html>
<html lang="en">
<head>
<meta charset="utf-8">
<title>Zelquin Business Card</title>
<link href="https://fonts.googleapis.com/css2?family=Open+Sans:wght@400;600;700&display=swap" rel="stylesheet">
<style>
  :root {
    --backdrop: #3a3a3a;
    --card-dark: #262626;
    --card-panel: #2a2a2b;
    --curve-edge: #3b3f40;
    --front-mark: #161616;
    --teal: #44b3b6;
    --white: #ffffff;
  }
  html, body {
    margin: 0;
    padding: 0;
    width: 799px;
    height: 1200px;
    overflow: hidden;
    background: var(--backdrop);
    font-family: "Open Sans", Arial, sans-serif;
  }
  .canvas {
    position: relative;
    width: 799px;
    height: 1200px;
  }
  .card {
    position: absolute;
    left: 80px;
    width: 640px;
    height: 366px;
    border-radius: 26px;
    overflow: hidden;
    box-shadow: 0 14px 30px rgba(0,0,0,0.45);
  }
  .card--front { top: 150px; background: var(--card-dark); }
  .card--back { top: 684px; }
  .front-wordmark {
    position: absolute;
    inset: 0;
    display: flex;
    align-items: center;
    justify-content: center;
    font-weight: 600;
    font-size: 78px;
    letter-spacing: 4px;
    color: var(--front-mark);
  }
  .back-shape { position: absolute; inset: 0; }
  .identity {
    position: absolute;
    left: 36px;
    top: 36px;
    color: var(--white);
  }
  .identity__name { font-size: 24px; font-weight: 700; margin: 0; }
  .identity__title { font-size: 13px; font-weight: 400; margin: 2px 0 0; }
  .contacts {
    position: absolute;
    left: 36px;
    bottom: 36px;
    list-style: none;
    margin: 0;
    padding: 0;
    color: var(--white);
    font-size: 15px;
  }
  .contacts li { display: flex; align-items: center; gap: 10px; height: 24px; }
  .contacts svg { width: 17px; height: 17px; flex: none; }
  .back-wordmark {
    position: absolute;
    right: 34px;
    top: 150px;
    width: 290px;
    text-align: center;
    font-weight: 600;
    font-size: 56px;
    letter-spacing: 3px;
    color: var(--teal);
  }
</style>
</head>
<body>
<div class="canvas">
  <section class="card card--front">
    <div class="front-wordmark">ZELQUIN</div>
  </section>

  <section class="card card--back">
    <svg class="back-shape" viewBox="0 0 640 366" preserveAspectRatio="none">
      <rect width="640" height="366" fill="var(--teal)"/>
      <path d="M370 0 C300 60 250 200 232 366 L640 366 L640 0 Z" fill="var(--curve-edge)"/>
      <path d="M384 0 C316 62 268 200 252 366 L640 366 L640 0 Z" fill="var(--card-panel)"/>
    </svg>

    <div class="identity">
      <p class="identity__name">Elias Marlow Grant</p>
      <p class="identity__title">Managing Director</p>
    </div>

    <ul class="contacts">
      <li>
        <svg viewBox="0 0 20 20"><circle cx="10" cy="10" r="9" fill="none" stroke="#fff" stroke-width="1.6"/><path d="M7 5.5l1.6 0 .8 2.4-1.1.8a6 6 0 0 0 2.6 2.6l.8-1.1 2.4.8v1.6c0 .6-.6 1-1.2.9A7.5 7.5 0 0 1 6.1 6.7c-.1-.6.3-1.2.9-1.2z" fill="#fff"/></svg>
        <span>212.480.7316</span>
      </li>
      <li>
        <svg viewBox="0 0 20 20"><circle cx="10" cy="10" r="9" fill="none" stroke="#fff" stroke-width="1.6"/><rect x="5.5" y="7" width="9" height="6.5" fill="none" stroke="#fff" stroke-width="1.3"/><path d="M5.5 7l4.5 3.6L14.5 7" fill="none" stroke="#fff" stroke-width="1.3"/></svg>
        <span>elias@zelquin.com</span>
      </li>
      <li>
        <svg viewBox="0 0 20 20"><circle cx="10" cy="10" r="9" fill="none" stroke="#fff" stroke-width="1.6"/><circle cx="10" cy="10" r="5" fill="none" stroke="#fff" stroke-width="1.2"/><path d="M5 10h10M10 5c-2 3-2 7 0 10M10 5c2 3 2 7 0 10" fill="none" stroke="#fff" stroke-width="1"/></svg>
        <span>www.zelquin.com</span>
      </li>
    </ul>

    <div class="back-wordmark">ZELQUIN</div>
  </section>
</div>
</body>
</html>
```